Folder and brochures for food service software solution

We offer integrated software solutions for independent and chain food service businesses. Such businesses would include fine dining restaurants, fast food outlets, home delivery, takeaways, cafeterias, event catering venues, institutional catering companies, hotels with restaurants / bars, etc. Our software is configured for the needs of each type of business and spans both guest facing and back office functions.

The core benefits our solution offers is that it is -
1. integrated to cater to all the needs of the food service business, both independent and chain, across most (not all, we do not do anything for labor management) functions.
2. functionally powerful and compare well with the best available internationally.
3. Developed using the latest in software technology ... for example, our EPOS software for Android devices.

The market is a mature market with many competitors. A few very well established with huge track record. We have a track record internationally but are new to the UK market. This brochure is targeted at the UK market. The target market is jaded with the number of options available. We will focus on fine dining outlets in the hope that our Android based EPOS will excite them. We will focus on events & catering because the competition in the segment is relatively thin. We will go after the institutional catering market because we offer strong cost control features. But we want to mention how we service all sub-segments of the food & beverage service business to convey the versatility of our solution and for the other businesses that we may be able to attract.

We are hoping that the brochure will stand-out from the crowd and will compel the market to browse through what we do.

Some key competitors in the UK include -
http://www.venbrook.co.uk/
http://www.q-til.co.uk/
http://www.harromax.co.uk/
http://dunvey.co.uk/

We have a company and product logo (both attached). Of these, we are open to dropping or redesgning the product logo. We have also developed a web site (see kbuk.tarvensystems.example). The brochure design need not conform to the web site, if (and only if) you can come up with a really attention design (we could consider redesign of the web site).

The content of the brochure will largely conform to the content at the web site. The content at the web site is structured by solutions for independent outlets (centered around the EPOS) and solutions for chains. It also mentions 18 products. This is too much for a print brochure. So, we propose the following structure -

1. a folder that also carries a brief about our company with facility to add inserts.
2. one brochure that describes the solutions offered, the market segments they apply to and the benefits of the solution for each segment.
3. A summary / list of the products that are used to configure the solution.

We will add product specific flyers to the folder by color laser printing these. This will provide us the flexibility to add only the few product sheets that are of relevance to each prospect and will allow us to update frequently. For this we will require a template so that all product sheets look similar ... possibly with a color theme separating the products for each outlet from those for the chain of outlets.

We can only provide low-res images. You will have to touch up screens to improve resolution of images to make them print-ready. You are free to propose purchase of reasonably priced general stock-shots subject to prior approval from us. We will pay for these images.
Updates

At least one of you have requested that we -

1. identify a key message and

2. compact the contents of the brochure 

To do so, we have had to take an alternative approach and revise the content completely. Please check back and see the latest uploads, both Marlo - Approach 2 and Marlo - Salient Features.

We hope this helps you in your design effort.                     

Reason: We understand that we are requesting this design through a holiday season. We are extending the deadline by a few days. If this also does not work for some of you, please let us know a realistic date by which you are able to provide us options. We will consider, even though we are on a tight time line.

Reason: Some of you are still working on final layouts At least one of you is waiting for us to provide you modified content to fit the design. The extra days are intended to allow you to provide a complete and final design.

Earlier, we had posted an update and new content. This was in response to the community's request to reduce content. Did you note that? It seems not. So, we have now removed older content and only retained the revised content as per the last update. Please verify that the design you propose is as per the latest content. In the process, we may have removed some images also. Need them? Let me know and I will re-post.

Reason: Further extension, open only to those that have previously submitted designs and need the extra time to finalize the design based on feedback from us.

Target Market(s)

Upper mid market fine dining restaurants, likely with home delivery / takeaway options.
Small food service chains (3 to 10 outlets).
Venues with catering facilities.
Cafeterias.
Bulk food suppliers / institutional caterers.
Food service business with a central kitchen / commissary and multiple service locations.
membership clubs with food service.

Industry/Entity Type

Software

Font styles to use
Sans Serif

Requirements
Must have
• A distinctive attention grabbing design.

The structure of -
1. a folder with facility for inserts.
2. two brochures.
3. template for product specific write-ups.
Nice to have
• Info-graphics to represent an integrated solution. Another to demonstrate versatility across types of F&B business.

A design that relates the solution to the UK ... either in terms of colors or visuals.

```html
<!DOCTYPE html>
<html lang="en">
<head>
<meta charset="utf-8">
<title>Marlo – Service Types</title>
<link rel="stylesheet" href="https://fonts.googleapis.com/css2?family=Titillium+Web:wght@300;400;600&display=swap">
<style>
  :root {
    --brand-red: #a3161f;
    --band-red: #e0232b;
    --text-grey: #4d4d4d;
    --page-top: #ffffff;
    --page-bottom: #dedede;
  }
  * { margin: 0; padding: 0; box-sizing: border-box; }
  html, body { width: 841px; height: 1200px; overflow: hidden; }
  body {
    position: relative;
    background: linear-gradient(180deg, var(--page-top) 0%, var(--page-top) 55%, var(--page-bottom) 100%);
    font-family: "Titillium Web", sans-serif;
    color: var(--text-grey);
  }
  .service-photo {
    position: absolute;
    left: 0;
    width: 310px;
  }
  .service-copy {
    position: absolute;
    left: 331px;
    width: 500px;
  }
  .service-title {
    font-weight: 600;
    font-size: 31px;
    line-height: 1;
    color: var(--brand-red);
  }
  .service-points {
    list-style: none;
    position: absolute;
    left: 0;
    width: 500px;
  }
  .service-points li {
    position: relative;
    padding-left: 9px;
    font-weight: 300;
    font-size: 13.2px;
    line-height: 16px;
    white-space: nowrap;
  }
  .service-points li::before {
    content: "";
    position: absolute;
    left: 0;
    top: 7px;
    width: 3.5px;
    height: 3.5px;
    background: var(--text-grey);
  }
  .brand-mark {
    position: absolute;
    left: 520px;
    top: 1070px;
  }
  .brand-name {
    font-weight: 600;
    font-size: 68px;
    line-height: 1;
    color: var(--text-grey);
  }
</style>
</head>
<body>

<svg class="service-photo" style="top:33px" width="310" height="205" viewBox="0 0 310 205" role="img" aria-label="Photo of a smiling delivery man in a red cap holding pizza boxes">
  <defs><linearGradient id="g1" x1="0" y1="0" x2="1" y2="1"><stop offset="0" stop-color="#8a6a5a"/><stop offset="0.6" stop-color="#7a2a30"/><stop offset="1" stop-color="#e8e4df"/></linearGradient></defs>
  <polygon points="0,0 287,0 258,205 0,205" fill="url(#g1)"/>
  <polygon points="287,0 307,0 278,205 258,205" fill="var(--band-red)"/>
</svg>
<section class="service-copy" style="top:27px">
  <h2 class="service-title">Home Delivery</h2>
  <ul class="service-points" style="top:38px">
    <li>Database of home delivery customers with their location and directions.</li>
    <li>Ability to look up past orders for suggestive selling and/or repeat ordering.</li>
    <li>Ability to take orders for delivery at alternative address or at specified time.</li>
    <li>Tracking of dispatch and delivery of each order.</li>
    <li>Statistics per delivery person.</li>
  </ul>
</section>

<svg class="service-photo" style="top:264px" width="310" height="206" viewBox="0 0 310 206" role="img" aria-label="Photo of a smiling woman with a takeaway cup and paper bag at an outdoor table">
  <defs><linearGradient id="g2" x1="0" y1="0" x2="1" y2="1"><stop offset="0" stop-color="#7f9a5a"/><stop offset="0.55" stop-color="#a4896d"/><stop offset="1" stop-color="#cfc6b8"/></linearGradient></defs>
  <polygon points="0,0 287,0 258,206 0,206" fill="url(#g2)"/>
  <polygon points="287,0 307,0 278,206 258,206" fill="var(--band-red)"/>
</svg>
<section class="service-copy" style="top:271px">
  <h2 class="service-title">Take away</h2>
  <ul class="service-points" style="top:30px">
    <li>A seated dining outlet does not need an additional EPOS for takeaway orders.<br>&nbsp;The same EPOS can serve both and yet track revenues by each type of service.</li>
    <li>Repeat customers are tracked to identify high volume customers for special<br>&nbsp;handling.</li>
    <li>Order taking is made more efficient by allowing repeat of past orders.</li>
  </ul>
</section>

<svg class="service-photo" style="top:497px" width="310" height="208" viewBox="0 0 310 208" role="img" aria-label="Photo of a tray of chocolate dessert slices topped with berries">
  <defs><linearGradient id="g3" x1="0" y1="0" x2="1" y2="1"><stop offset="0" stop-color="#8c2a2e"/><stop offset="0.5" stop-color="#5a3324"/><stop offset="1" stop-color="#d7dadc"/></linearGradient></defs>
  <polygon points="0,0 287,0 258,208 0,208" fill="url(#g3)"/>
  <polygon points="287,0 307,0 278,208 258,208" fill="var(--band-red)"/>
</svg>
<section class="service-copy" style="top:502px;left:327px">
  <h2 class="service-title">Events &amp; Catering</h2>
  <ul class="service-points" style="top:45px">
    <li>Space booking diary.</li>
    <li>Track inquiries till converted to contract or lost.</li>
    <li>Custom menus and ad-hoc pricing.</li>
    <li>Prepare contracts and function sheets.</li>
    <li>Invoice through any Marlo EPOS. Even one that is in use for alternative<br>&nbsp;service</li>
  </ul>
</section>

<svg class="service-photo" style="top:731px" width="310" height="207" viewBox="0 0 310 207" role="img" aria-label="Photo of two smiling waiting staff in black waistcoats serving drinks">
  <defs><linearGradient id="g4" x1="0" y1="0" x2="1" y2="1"><stop offset="0" stop-color="#d9d2c8"/><stop offset="0.5" stop-color="#3a3232"/><stop offset="1" stop-color="#b5aca2"/></linearGradient></defs>
  <polygon points="0,0 287,0 258,207 0,207" fill="url(#g4)"/>
  <polygon points="287,0 307,0 278,207 258,207" fill="var(--band-red)"/>
</svg>
<section class="service-copy" style="top:738px;left:327px">
  <h2 class="service-title">Contract Catering</h2>
  <ul class="service-points" style="top:39px">
    <li>Sophisticated and integrated web based purchase, inventory, costing and<br>&nbsp;accounting software.</li>
    <li>Monitor kitchen and purchase efficiency.</li>
    <li>Menu engineering.</li>
  </ul>
</section>

<svg class="service-photo" style="top:963px" width="310" height="211" viewBox="0 0 310 211" role="img" aria-label="Photo of a cup of coffee beside a wooden box of coffee beans">
  <defs><linearGradient id="g5" x1="0" y1="0" x2="1" y2="1"><stop offset="0" stop-color="#6b4a2e"/><stop offset="0.55" stop-color="#3b2617"/><stop offset="1" stop-color="#e9e4dd"/></linearGradient></defs>
  <polygon points="0,0 287,0 258,211 0,211" fill="url(#g5)"/>
  <polygon points="287,0 307,0 278,211 258,211" fill="var(--band-red)"/>
</svg>
<section class="service-copy" style="top:954px;left:327px">
  <h2 class="service-title">Cafeterias</h2>
  <ul class="service-points" style="top:54px">
    <li>Cashless operations by use of stored value cards or by integration with payroll<br>&nbsp;system or credit sales accounting.</li>
    <li>Better control over F&amp;B costs.</li>
  </ul>
</section>

<div class="brand-mark">
  <span class="brand-name">Marlo</span>
</div>

</body>
</html>
```